Shipping and Logistics, Project

Project description : Company Profile

A total logistics company covering domestic / international freight forwarding, warehouse management services, haulage, supply chain management, transport management & distribution, procurement & assembly services, shipping, chartering & bunker services, project logistics & tax exemption consultancy, oil & gas logistics, halal logistics services & integrated logistics management. We’re a well-established and experienced freight forwarder in Kuala Lumpur, Malaysia. We specialize in customized value-added solution that optimizes your supply chain by trimming inventory, reducing logistics cost and enhancing your customer service levels.

As a member of the Worldwide Parcel and Carriage Alliance which comprise of 170 global freight agents in 80 countries that promotes great handling in cross-trade logistics and freighting. You could rely on our efficiency in handlings of export cargo (FCL, LCL, Bulk and Conventional) between our global network offices worldwide with a total scale of 10,000 groomed specialists in various logistics division working together to ensure delivery task meets with your expectation. With our dedicated qualified and experienced professionals, we are fully committed to serving our clients.

Our generic services are listed below for your reference:

• Air Freight
• Ocean Freight FCL & LCL
• Container Haulage
• Warehousing
• Transportation and Distribution within Malaysia and Thailand
• Cross-Border Road Line-hauls between Thailand, Malaysia, Singapore and Laos
• Customs Brokerage and Forwarding
• Project Cargo Freight Forwarding for setting up of new plants / factories and ad hoc heavy-lift
• Air-Sea-Road-Rail multi-modal options
• Import / Export / Storage / Documentation / Handling of DG / Hazmat
• Vessel and Aircraft Charters

Our Mission
Based on the motto “Quick, Reliable and Polite”, we are dedicated to upholding the following three points corporate philosophy:
1. Adhering to the principle that “the customer always comes first”.
2. Contributing to the development of the local community.
3. Making it our duty to be responsible and sincere.

Our Edge
• One-Stop Logistics Solutions
• Extensive Network Throughout Malaysia
• Highly Qualified and Experienced Pool of Professionals
• Comprehensive IT Solutions
• Innovative and Customer-focused Solutions
• Flexible and Consistent in Managing Exceptions
• Total Supply Chain Visibility

Target Market
1. We sell the logistics services to all the industry in Malaysia and Worldwide. (ONE Stop Logistics Solutions)

Competitor
1. TR Valmont
2. Corvessa Transport
3. Brandt + Loewe
4. FELRO
5. QTV
6. Routemarks
7. Ilto Logistics

Rules for Picking a Company Name
1. Unique and unforgettable
2. Avoid unusual spellings
3. Easy to pronounce and remember
4. Keep it simple
5. Make some sense
6. Give a clue

Rules for Picking a Company Logo
4. Keep it simple
5. Make some sense
6. Give a clue

1. Simplicity
2. Memorability
3. Originality
4. Modern Yet Timeless
5. Balance
6. Complementary
7. Versatility

Stationery Information
1. Company Name : ZENFreight Solutions Sdn Bhd
2. Company Registration : 2837165-W
3. Address : 42-08, Jalan Cempaka Indah 5, Taman Seri Bayu, 81300 Johor Bahru, Johor, Malaysia.
4. Name : Derek Tan
5. Position : Manager
6. Mobile No : (+6019) 4381907
7. Office No : (+607) 5218764
8. Fax No : Not Available
9. Email Address : derek.tan@zenfreight-solutions.example
10. Web Domain : www.zenfreight-solutions.example
11. Company Slogan : Be Globally Connected

Target Market(s)

Corporate Company

Industry/Entity Type

Shipping and Logistics Industry

Requirements
Must have
• Company Full Name : ZENFREIGHT SOLUTIONS SDN. BHD.
Nice to have
• Keep it simple and unforgettable ...

```html
<!DOCTYPE html>
<html lang="en">
<head>
<meta charset="utf-8">
<title>ZENFreight Solutions – Business Card</title>
<link rel="stylesheet" href="https://fonts.googleapis.com/css2?family=Montserrat:wght@600;700;800&family=Open+Sans:wght@400;600&display=swap">
<style>
  :root {
    --brand-blue: #2f86dd;
    --brand-blue-deep: #2a7ccf;
    --ink: #1c1c1c;
    --band-black: #222222;
    --paper: #ffffff;
    --mist: #efefef;
    --rule: #b9b9b9;
    --stage: #d9d9d9;
  }
  * { box-sizing: border-box; margin: 0; padding: 0; }
  html, body { width: 1200px; height: 800px; overflow: hidden; }
  body {
    background: var(--stage);
    font-family: "Open Sans", Arial, sans-serif;
    color: var(--ink);
    display: flex;
    align-items: center;
    justify-content: center;
    gap: 40px;
  }
  .card {
    position: relative;
    width: 540px;
    height: 308px;
    border-radius: 18px;
    overflow: hidden;
    box-shadow: 0 10px 28px rgba(0,0,0,.22);
  }

  /* Front */
  .card-front { background: var(--paper); }
  .front-decor {
    position: absolute;
    left: 0; top: 110px;
    width: 170px; height: 150px;
    background: linear-gradient(135deg, var(--mist), #f7f7f7);
  }
  .brand {
    position: absolute;
    left: 30px; top: 118px;
    display: flex; align-items: center; gap: 10px;
  }
  .brand-mark {
    width: 30px; height: 30px;
    background: var(--brand-blue);
  }
  .brand-name {
    font-family: "Montserrat", Arial, sans-serif;
    font-weight: 700;
    font-size: 13px;
    line-height: 1.25;
    letter-spacing: .5px;
    color: var(--brand-blue);
    width: 150px;
  }
  .divider {
    position: absolute;
    left: 218px; top: 30px;
    width: 1px; height: 200px;
    background: var(--rule);
  }
  .contact {
    position: absolute;
    left: 240px; top: 30px;
    width: 290px;
  }
  .person-name {
    font-family: "Montserrat", Arial, sans-serif;
    font-weight: 800;
    font-size: 22px;
    letter-spacing: .3px;
    color: var(--ink);
  }
  .person-name .surname { color: var(--brand-blue); }
  .person-role { font-size: 12px; margin-top: 0; }
  .contact-list { list-style: none; margin-top: 10px; }
  .contact-list li {
    display: flex; align-items: center; gap: 8px;
    font-size: 11px; line-height: 18px;
  }
  .contact-list svg { width: 11px; height: 11px; flex: none; fill: var(--brand-blue); }
  .contact-list .accent { color: var(--brand-blue); }
  .address { font-size: 11px; line-height: 16px; margin-top: 10px; width: 240px; }

  .band {
    position: absolute;
    left: 0; bottom: 0;
    width: 100%; height: 46px;
  }
  .band-black {
    position: absolute; left: 0; bottom: 8px;
    width: 250px; height: 38px;
    background: var(--band-black);
    clip-path: polygon(0 0, 100% 0, 94% 100%, 0 100%);
    color: #fff;
    font-size: 12px;
    display: flex; align-items: center; padding-left: 22px;
  }
  .band-line {
    position: absolute; left: 0; bottom: 0;
    width: 100%; height: 8px; background: var(--brand-blue);
  }
  .band-blue {
    position: absolute; right: 0; bottom: 0;
    width: 300px; height: 46px;
    background: var(--brand-blue);
    clip-path: polygon(4% 0, 100% 0, 100% 100%, 0 100%);
    color: #fff;
    font-family: "Montserrat", Arial, sans-serif;
    font-weight: 700;
    font-size: 15px;
    letter-spacing: .6px;
    display: flex; align-items: center; justify-content: flex-end; padding-right: 26px;
  }

  /* Back */
  .card-back { background: var(--brand-blue); }
  .back-pattern {
    position: absolute; inset: 0;
    background: linear-gradient(135deg, var(--brand-blue-deep), var(--brand-blue) 60%, #3a93e6);
  }
  .back-brand {
    position: absolute;
    left: 50%; top: 50%;
    transform: translate(-50%, -50%);
    display: flex; align-items: center; gap: 12px;
  }
  .back-brand .brand-mark { width: 36px; height: 36px; background: #fff; }
  .back-brand .brand-name { color: #fff; font-size: 15px; width: 180px; }
</style>
</head>
<body>
  <section class="card card-front">
    <div class="front-decor" role="img" aria-label="Faint oversized brand symbol watermark"></div>
    <div class="brand">
      <span class="brand-mark"></span>
      <span class="brand-name">ZENFREIGHT SOLUTIONS SDN. BHD.</span>
    </div>
    <div class="divider"></div>
    <div class="contact">
      <h1 class="person-name">DEREK <span class="surname">TAN</span></h1>
      <p class="person-role">Manager</p>
      <ul class="contact-list">
        <li><svg viewBox="0 0 12 12"><rect x="3" y="0.5" width="6" height="11" rx="1.2"/></svg>(+6019) 4381907</li>
        <li><svg viewBox="0 0 12 12"><path d="M2.5 1 4.5 1 5.5 3.8 4.2 4.8A7 7 0 0 0 7.2 7.8L8.2 6.5 11 7.5 11 9.5C11 10.3 10.3 11 9.5 11 5 11 1 7 1 2.5 1 1.7 1.7 1 2.5 1Z"/></svg>(+607) 5218764</li>
        <li><svg viewBox="0 0 12 12"><path d="M0.5 2.5h11v7h-11z M0.5 2.5 6 6.8 11.5 2.5" fill="none" stroke="#2f86dd" stroke-width="1.3"/></svg>derek.tan@zenfreight-solutions.example</li>
        <li><svg viewBox="0 0 12 12"><circle cx="6" cy="6" r="5" fill="none" stroke="#2f86dd" stroke-width="1.2"/><path d="M1 6h10M6 1c-2.6 3-2.6 7 0 10M6 1c2.6 3 2.6 7 0 10" fill="none" stroke="#2f86dd" stroke-width="1"/></svg>www.<span class="accent">zenfreight-solutions</span>.example</li>
      </ul>
      <p class="address">42-08, Jalan Cempaka Indah 5, Taman Seri Bayu, 81300 Johor Bahru, Johor, Malaysia</p>
    </div>
    <div class="band">
      <div class="band-line"></div>
      <div class="band-black">Company No. 2837165-W</div>
      <div class="band-blue">BE GLOBALLY CONNECTED</div>
    </div>
  </section>

  <section class="card card-back">
    <div class="back-pattern" role="img" aria-label="Embossed repeating brand symbol pattern in blue tones"></div>
    <div class="back-brand">
      <span class="brand-mark"></span>
      <span class="brand-name">ZENFREIGHT SOLUTIONS SDN. BHD.</span>
    </div>
  </section>
</body>
</html>
```